Motel Sign - Front

(21/03/12 - I've edited the brief and removing the words "garden view" its not fitting in the designs I'm getting and just want the word motel to be the focus. I have a template/vision of what I want - see the whiteboard sketch of what I'm looking for uploaded today. Definitely open to creatively, new designs and different ideas but the whiteboard design I've done should be a guideline. Keep it fresh/green/white. use the sample photos of green as inspiration. Thanks)
We are a motel set in the mountain country of Victoria - Australia. The front of the motel needs a fresh look. We recently removed a large amount of the garden to expose a brick courtyard fence which the front of the courtyard faces out to the main road. Within the courtyard fence there is a wooden frame and paneling.
We want to have a new sign created to slot into the wooden frame. (see photo) its the white component.
Its a very large and unusual shape and I want to keep it simple but need to fill the in the best way possible.
The space is 940mm high and 4940mm width.
The message of the sign is simple the word "MOTEL". I want people to be able to drive past and glance in and see we are a motel straight away. So the main purpose of the sign is to say "MOTEL".
I am open to colour use to match the space and have impact. I thought a background colour should be 'off white'. I'm open to the colours used to match your design as long as it matches the brief. Maybe a garden green for the emblem.
IN BRIEF:
1) the word "MOTEL"
2) Border/Background that ties in the garden.
The design should be centred, clean and simple, doesn't have to fill the whole space as long as its balanced and centred.
I like cursive and garden like designs for this one - as long its the word MOTEL still has impact. (OPEN TO NEW IDEAS)
I am also open to different ideas and suggestions if you feel you have a better way to take advantage of this space.
The sign will be 7-8 metres from the road itself.
NOTE: the photos show the space and the painted white in the space where the sign will go. The garden in front of this space will be completely cleared.
Motel

```html
<!DOCTYPE html>
<html lang="en">
<head>
<meta charset="utf-8">
<title>Motel Sign</title>
<link rel="stylesheet" href="https://fonts.googleapis.com/css2?family=Great+Vibes&display=swap">
<style>
  :root {
    --green-deep: #24420f;
    --green-mid: #3f6a1c;
    --green-bright: #5f8f2a;
    --green-leaf: #8fbf4a;
    --green-edge: #9cc45a;
    --lime-glow: #c6e06a;
    --text-white: #ffffff;
  }
  * { margin: 0; padding: 0; box-sizing: border-box; }
  html, body {
    width: 1200px;
    height: 230px;
    overflow: hidden;
    background: var(--green-deep);
  }
  .sign {
    position: relative;
    width: 1200px;
    height: 230px;
    overflow: hidden;
    background:
      radial-gradient(ellipse 55% 90% at 50% 50%, var(--green-bright) 0%, var(--green-mid) 45%, var(--green-deep) 100%);
  }
  .sign__edge {
    position: absolute;
    left: 0;
    width: 100%;
    height: 10px;
    background: linear-gradient(90deg, var(--green-edge), var(--green-leaf) 50%, var(--green-edge));
    opacity: 0.55;
  }
  .sign__edge--top { top: 0; }
  .sign__edge--bottom { bottom: 0; }
  .sign__garden {
    position: absolute;
    top: 0;
    height: 230px;
  }
  .sign__garden--left {
    left: 0;
    width: 320px;
    background: linear-gradient(90deg, rgba(143,191,74,0.75) 0%, rgba(143,191,74,0.45) 55%, rgba(143,191,74,0) 100%);
  }
  .sign__garden--right {
    right: 0;
    width: 240px;
    background: linear-gradient(270deg, rgba(143,191,74,0.75) 0%, rgba(143,191,74,0.45) 55%, rgba(143,191,74,0) 100%);
  }
  .sign__title {
    position: absolute;
    left: 0;
    top: 0;
    width: 100%;
    height: 230px;
    display: flex;
    align-items: center;
    justify-content: center;
    font-family: "Great Vibes", cursive;
    font-weight: 400;
    font-size: 178px;
    line-height: 1;
    color: var(--text-white);
    -webkit-text-stroke: 2px var(--lime-glow);
    text-shadow: 0 0 6px rgba(198,224,106,0.8), 2px 3px 2px rgba(20,40,8,0.6);
    padding-top: 6px;
  }
</style>
</head>
<body>
  <div class="sign">
    <div class="sign__edge sign__edge--top"></div>
    <div class="sign__garden sign__garden--left" role="img" aria-label="Light green clover and flourish garden ornament"></div>
    <div class="sign__garden sign__garden--right" role="img" aria-label="Light green clover and flourish garden ornament"></div>
    <h1 class="sign__title">Motel</h1>
    <div class="sign__edge sign__edge--bottom"></div>
  </div>
</body>
</html>
```